Builder of high-end, expensive tables and other furniture

Build a website that represents what we do. I want a luxury feel that appeals to those who can afford our products. We build very high end tables and other furniture using trees that have fallen or are standing dead. We never cut living trees. Trees are harvested, milled, and kiln dried. Then that lumber is meticulously turned into fine furniture using the best equipment. Our furniture prices range from $1,000-$20,000.

Trying to figure out how to raise my spend.

```html
<!DOCTYPE html>
<html lang="en">
<head>
<meta charset="utf-8">
<title>Heartwood Row — Fine Furniture from Fallen Trees</title>
<link rel="stylesheet" href="https://fonts.googleapis.com/css2?family=EB+Garamond:wght@400;500;600;700;800&display=swap">
<style>
:root{
  --orange:#f07a22;
  --orange-soft:#f4a56a;
  --blue:#0a51a6;
  --ink:#111111;
  --white:#ffffff;
  --grey-band:#dcdcdd;
  --card:#f9f9f9;
  --field-line:#d6d6d6;
  --footer:#000000;
}
*{box-sizing:border-box;margin:0;padding:0}
html,body{width:1200px;height:3344px;overflow:hidden}
body{font-family:"EB Garamond",Georgia,serif;color:var(--ink);background:var(--white);position:relative}
.abs{position:absolute}

/* hero */
.hero{position:absolute;left:0;top:0;width:1200px;height:610px;overflow:hidden}
.hero-photo{position:absolute;inset:0;background:
  linear-gradient(180deg,#fbf6ee 0%,#e9d7bd 18%,#b88a52 40%,#5d6a3a 62%,#3b3a24 80%,#6b4b2b 100%)}
.hero-photo::before{content:"";position:absolute;left:0;top:220px;width:330px;height:390px;background:linear-gradient(160deg,#8a5a33,#3a2a1c)}
.hero-photo::after{content:"";position:absolute;right:0;top:200px;width:330px;height:410px;background:linear-gradient(200deg,#c07a3e,#3a2a1c)}
.hero-wave{position:absolute;left:0;bottom:0;width:1200px;height:60px}
.brand{position:absolute;font-weight:700;color:var(--orange);letter-spacing:.5px}
.brand-mark{display:inline-block;width:14px;height:14px;border-radius:50%;background:var(--orange);margin-right:8px;vertical-align:middle}
.top-brand{left:100px;top:30px;font-size:34px}
.top-nav{position:absolute;top:36px;left:0;width:1200px;font-size:16px;color:var(--ink)}
.top-nav a{position:absolute;color:inherit;text-decoration:none}
.hero-kicker{position:absolute;top:170px;width:1200px;text-align:center;font-size:54px;font-weight:400;letter-spacing:1px;color:#111}
.hero-title{position:absolute;top:240px;width:1200px;text-align:center;font-size:76px;font-weight:800;letter-spacing:-1px;color:#0a0a0a}

/* buttons */
.btn{position:absolute;display:flex;align-items:center;justify-content:center;width:206px;height:57px;color:var(--white);font-weight:700;font-size:25px;background:var(--orange);
  clip-path:polygon(14px 0,calc(100% - 14px) 0,100% 50%,calc(100% - 14px) 100%,14px 100%,0 50%)}

/* about */
.about-decor{position:absolute;left:90px;top:660px;width:445px;height:280px;border-radius:50% 50% 0 0;background:radial-gradient(ellipse at 50% 80%,rgba(240,122,34,.0) 45%,rgba(240,122,34,.35) 70%,rgba(240,122,34,0) 90%)}
.about-photo{position:absolute;left:104px;top:734px;width:416px;height:416px;border-radius:50%;
  background:radial-gradient(circle at 50% 30%,#9aa08e 0%,#6d6a55 35%,#8a5d3a 65%,#4e3522 100%);border-bottom:6px solid var(--orange-soft)}
.section-title{position:absolute;font-size:44px;font-weight:700;letter-spacing:.3px;color:var(--ink)}
.about-copy{position:absolute;left:603px;top:780px;width:430px;font-size:14px;line-height:30px;color:#222}
.about-trace{position:absolute;right:0;top:1070px;width:360px;height:165px;background:radial-gradient(ellipse at 70% 80%,rgba(240,122,34,.12),rgba(240,122,34,0) 70%)}

/* furniture */
.furniture{position:absolute;left:0;top:1235px;width:1200px;height:560px;background:linear-gradient(180deg,#e2e2e3,#d6d6d8)}
.card{position:absolute;top:168px;width:236px;height:269px;background:var(--card);border-radius:10px;padding:4px}
.card-photo{width:228px;height:156px;border-radius:8px}
.card-name{position:absolute;left:15px;top:178px;font-size:25px;font-weight:400}
.card-price{position:absolute;left:19px;top:218px;font-size:25px;font-weight:700}

/* process */
.step{position:absolute;top:1986px;width:216px;height:222px}
.step-disc{position:absolute;left:0;top:0;width:216px;height:216px;border-radius:50%;background:var(--blue);box-shadow:0 6px 0 var(--orange-soft)}
.step-disc svg{position:absolute;left:48px;top:48px}
.step-label{position:absolute;top:2228px;width:300px;text-align:center;font-size:25px;font-weight:700}

/* contact */
.field-label{position:absolute;font-size:19px;color:#222}
.field{position:absolute;border:2px solid var(--field-line);border-radius:12px;background:var(--white)}
.consent-box{position:absolute;left:626px;top:2702px;width:28px;height:28px;border:2px solid #bdbdbd;border-radius:7px}
.consent-text{position:absolute;left:673px;top:2700px;width:450px;font-size:15px;line-height:23px;color:#222}

/* footer */
.footer{position:absolute;left:0;top:2880px;width:1200px;height:464px}
.footer-fringe{position:absolute;left:0;top:0;width:1200px;height:60px;background:linear-gradient(180deg,rgba(244,165,106,0),rgba(244,165,106,.35))}
.footer-wave{position:absolute;left:0;top:20px;width:1200px;height:60px}
.footer-body{position:absolute;left:0;top:70px;width:1200px;height:394px;background:var(--footer)}
.footer-brand{left:0;width:1200px;text-align:center;top:3040px;font-size:60px}
.footer-nav{position:absolute;top:3160px;left:0;width:1200px;font-size:21px;color:var(--white)}
.footer-nav a{position:absolute;color:inherit;text-decoration:none}
.footer-rule{position:absolute;left:95px;top:3236px;width:1004px;height:1px;background:#8a8a8a}
.copyright{position:absolute;top:3268px;width:1200px;text-align:center;font-size:19px;color:var(--white)}
</style>
</head>
<body>

<header class="hero">
  <div class="hero-photo" role="img" aria-label="Stacked logs beside a forest road winding into sunlit mountains"></div>
  <svg class="hero-wave" viewBox="0 0 1200 60" preserveAspectRatio="none" aria-hidden="true">
    <path d="M0 52 C60 70 90 20 160 40 C230 60 280 28 360 44 C440 60 500 30 580 42 C660 54 720 20 800 36 C880 52 940 24 1020 38 C1100 52 1150 30 1200 40 L1200 60 L0 60Z" fill="#ffffff"/>
  </svg>
  <div class="brand top-brand"><span class="brand-mark"></span>Heartwood Row</div>
  <nav class="top-nav">
    <a style="left:500px">Home</a><a style="left:593px">About Us</a><a style="left:713px">Furniture</a>
    <a style="left:827px">Products</a><a style="left:937px">Prices</a><a style="left:1026px">Contact Us</a>
  </nav>
  <div class="hero-kicker">WELCOME TO</div>
  <h1 class="hero-title">HEARTWOOD ROW</h1>
  <div class="btn" style="left:497px;top:348px">Get Started</div>
</header>

<section class="about">
  <div class="about-decor" role="img" aria-label="Bare orange tree branches framing the photo"></div>
  <div class="about-photo" role="img" aria-label="Felled logs lying on a forest floor among tall pines"></div>
  <h2 class="section-title" style="left:603px;top:706px">ABOUT US</h2>
  <p class="about-copy">Sed ut perspiciatis unde omnis iste natus error sit voluptatem accusantium doloremque laudantium, totam rem aperiam, eaque ipsa quae ab illo inventore veritatis et quasi architecto beatae vitae dicta sunt explicabo. Nemo enim ipsam voluptatem quia voluptas sit aspernatur aut odit aut fugit, sed quia consequuntur magni dolores eos qui ratione voluptatem sequi nesciunt. Neque porro quisquam est, qui dolorem ipsum quia dolor sit amet, consectetur, adipisci velit, sed quia non numquam eius modi tempora incidunt ut labore et dolore magnam aliquam quaerat voluptatem.</p>
  <div class="btn" style="left:595px;top:1078px">Read More</div>
  <div class="about-trace" role="img" aria-label="Faint tree branch decoration"></div>
</section>

<section class="furniture" role="region" aria-label="Our furniture">
  <h2 class="section-title" style="left:0;width:1200px;text-align:center;top:70px">OUR FURNITURE</h2>
  <div class="card" style="left:101px">
    <div class="card-photo" role="img" aria-label="Tan leather sofa in a bright room" style="background:linear-gradient(180deg,#ece6e0 55%,#b98a52 56%,#d4c2ab 85%)"></div>
    <div class="card-name">Sofa</div><div class="card-price">$ 950.00</div>
  </div>
  <div class="card" style="left:356px">
    <div class="card-photo" role="img" aria-label="Wooden outdoor table and lounge on a planted terrace" style="background:linear-gradient(180deg,#cfd7c8 30%,#6f8a4e 45%,#a9784a 70%,#d8cdb8)"></div>
    <div class="card-name">Tables</div><div class="card-price">$ 20,000.00</div>
  </div>
  <div class="card" style="left:610px">
    <div class="card-photo" role="img" aria-label="Upholstered bed with grey linens" style="background:linear-gradient(180deg,#e9e4de 25%,#a99a8c 45%,#d9d3cc 65%,#8a7565)"></div>
    <div class="card-name">Beds</div><div class="card-price">$ 5000.00</div>
  </div>
  <div class="card" style="left:864px">
    <div class="card-photo" role="img" aria-label="Dining table with black chairs under a pendant lamp" style="background:linear-gradient(180deg,#9c9c98 55%,#3a342e 70%,#dedbd6 85%)"></div>
    <div class="card-name">Dining table</div><div class="card-price">$ 5000.00</div>
  </div>
</section>

<section class="process">
  <h2 class="section-title" style="left:0;width:1200px;text-align:center;top:1878px">HOW ITS WORKS</h2>
  <div class="step" style="left:166px"><div class="step-disc">
    <svg width="120" height="120" viewBox="0 0 120 120" fill="none" stroke="#fff" stroke-width="5" stroke-linejoin="round" stroke-linecap="round" aria-label="Harvest icon" role="img">
      <path d="M10 30 H80 V60 H90 L110 90 H20 V60 H10 Z"/><circle cx="30" cy="92" r="9"/><circle cx="78" cy="92" r="11"/><path d="M80 30 H100 V50"/>
    </svg></div></div>
  <div class="step" style="left:499px"><div class="step-disc">
    <svg width="120" height="120" viewBox="0 0 120 120" fill="none" stroke="#fff" stroke-width="5" stroke-linejoin="round" stroke-linecap="round" aria-label="Milling icon" role="img">
      <rect x="54" y="10" width="40" height="14"/><path d="M62 24 V50 L74 64 L86 50 V24"/><path d="M20 80 H108 V104 H20 Z"/><path d="M24 14 C34 30 14 40 28 58"/>
    </svg></div></div>
  <div class="step" style="left:830px"><div class="step-disc">
    <svg width="120" height="120" viewBox="0 0 120 120" fill="none" stroke="#fff" stroke-width="5" stroke-linejoin="round" stroke-linecap="round" aria-label="Kiln icon" role="img">
      <path d="M14 108 V62 A46 46 0 0 1 106 62 V108 Z"/><path d="M36 108 V70 A24 24 0 0 1 84 70 V108"/><rect x="50" y="6" width="20" height="12"/><path d="M46 84 L54 72 L60 82 L68 70 L74 84"/>
    </svg></div></div>
  <div class="step-label" style="left:124px">Harvested</div>
  <div class="step-label" style="left:457px">Milled</div>
  <div class="step-label" style="left:788px">kiln Dried</div>
</section>

<section class="contact">
  <h2 class="section-title" style="left:90px;top:2396px">CONTACT US</h2>
  <div class="field-label" style="left:100px;top:2490px">Name *</div>
  <div class="field" style="left:100px;top:2524px;width:488px;height:62px"></div>
  <div class="field-label" style="left:100px;top:2609px">Email address *</div>
  <div class="field" style="left:100px;top:2643px;width:488px;height:62px"></div>
  <div class="field-label" style="left:100px;top:2724px">Phone number *</div>
  <div class="field" style="left:100px;top:2758px;width:488px;height:62px"></div>
  <div class="field-label" style="left:624px;top:2488px">Message *</div>
  <div class="field" style="left:624px;top:2522px;width:476px;height:158px"></div>
  <div class="consent-box"></div>
  <div class="consent-text">I allow this website to store my submission so they can respond to my inquiry. *</div>
  <div class="btn" style="left:618px;top:2763px">Read More</div>
</section>

<footer class="footer">
  <div class="footer-fringe" role="img" aria-label="Faint orange tree branch border"></div>
  <svg class="footer-wave" viewBox="0 0 1200 60" preserveAspectRatio="none" aria-hidden="true">
    <path d="M0 20 C80 0 120 50 200 40 C280 30 330 10 420 28 C510 46 560 20 640 30 C720 40 780 12 860 20 C940 28 1000 50 1080 30 C1140 16 1170 20 1200 24 L1200 60 L0 60Z" fill="#000"/>
  </svg>
  <div class="footer-body"></div>
</footer>
<div class="brand footer-brand"><span class="brand-mark" style="width:20px;height:20px"></span>Heartwood Row</div>
<nav class="footer-nav">
  <a style="left:223px">Home</a><a style="left:341px">About Us</a><a style="left:490px">Furniture</a>
  <a style="left:632px">Products</a><a style="left:770px">Prices</a><a style="left:881px">Contact Us</a>
</nav>
<div class="footer-rule"></div>
<div class="copyright">© copyrights 2023 Heartwood Row | All Rights Reserved</div>

</body>
</html>
```